VOMRA Pty Ltd Business Card

Looking for a simple yet eye-catching double-sided business card design using my company logo on one side and contact details on the other.

Target Market(s)

Government

Industry/Entity Type

Communication Systems Engineering

Contact Information for Business Card

VOMRA Pty Ltd

Requirements
Nice to have
• Would be great to have a QR code so details can be scanned into contacts

```html
<!DOCTYPE html>
<html lang="en">
<head>
<meta charset="utf-8">
<title>VOMRA Pty Ltd Business Card</title>
<link href="https://fonts.googleapis.com/css2?family=Open+Sans:wght@400;600;700&display=swap" rel="stylesheet">
<style>
  :root {
    --ink: #333d43;
    --band: #353f45;
    --card: #ffffff;
    --backdrop: #e6e8ea;
    --rule: #5a6369;
    --band-text: #f2f4f5;
  }
  * { box-sizing: border-box; margin: 0; padding: 0; }
  html, body { width: 1200px; height: 780px; overflow: hidden; }
  body {
    background: var(--backdrop);
    font-family: "Open Sans", Arial, sans-serif;
    color: var(--ink);
    position: relative;
  }
  .card {
    position: absolute;
    top: 235px;
    width: 540px;
    height: 309px;
    background: var(--card);
    border-radius: 18px;
    overflow: hidden;
    box-shadow: 0 2px 8px rgba(0,0,0,.12);
  }
  .card--front { left: 40px; }
  .card--back { left: 620px; }

  .brand {
    position: absolute;
    display: flex;
    align-items: center;
    color: var(--ink);
    font-weight: 700;
  }
  .brand__dot {
    border-radius: 50%;
    background: var(--ink);
    flex: none;
  }
  .card--front .brand { left: 250px; top: 52px; font-size: 46px; letter-spacing: 3px; gap: 14px; }
  .card--front .brand__dot { width: 22px; height: 22px; }
  .card--back .brand { left: 0; right: 0; top: 112px; justify-content: center; font-size: 68px; letter-spacing: 5px; gap: 20px; }
  .card--back .brand__dot { width: 30px; height: 30px; }

  .person {
    position: absolute;
    right: 305px;
    top: 150px;
    text-align: right;
  }
  .person__name { font-size: 21px; font-weight: 700; line-height: 1.2; }
  .person__role { font-size: 14px; font-weight: 400; margin-top: 2px; }

  .divider {
    position: absolute;
    left: 252px;
    top: 150px;
    width: 1px;
    height: 92px;
    background: var(--rule);
  }

  .contacts {
    position: absolute;
    left: 270px;
    top: 168px;
    list-style: none;
    font-size: 15px;
    line-height: 25px;
  }
  .contacts li { display: flex; align-items: center; gap: 8px; }
  .contacts svg { width: 13px; height: 13px; fill: var(--ink); flex: none; }

  .address-band {
    position: absolute;
    left: 0; right: 0; bottom: 0;
    height: 40px;
    background: var(--band);
    color: var(--band-text);
    font-size: 15px;
    display: flex;
    align-items: center;
    padding-left: 26px;
    letter-spacing: .2px;
  }
</style>
</head>
<body>
  <section class="card card--front">
    <div class="brand"><span class="brand__dot"></span>VOMRA</div>

    <div class="person">
      <p class="person__name">Jordan Hale</p>
      <p class="person__role">Co-Founder</p>
    </div>

    <div class="divider"></div>

    <ul class="contacts">
      <li>
        <svg viewBox="0 0 16 16" aria-hidden="true"><path d="M3.6 1.2l2.3 2.5-1.3 2.1c.9 2 2.6 3.7 4.6 4.6l2.1-1.3 2.5 2.3-1.3 2.6C6.5 14 2 9.5 1 3.5z"/></svg>
        (555) 014-2236
      </li>
      <li>
        <svg viewBox="0 0 16 16" aria-hidden="true"><path d="M8 1a7 7 0 100 14A7 7 0 008 1zm0 1.5c.8 0 1.7 1.6 2 4H6c.3-2.4 1.2-4 2-4zM2.6 7h2c-.1 1 0 1.5 0 2h-2a5.5 5.5 0 010-2zm8.8 0h2a5.5 5.5 0 010 2h-2c.1-.5.1-1 0-2zM6 9.5h4c-.3 2.4-1.2 4-2 4s-1.7-1.6-2-4z"/></svg>
        www.vomra.com.au
      </li>
      <li>
        <svg viewBox="0 0 16 16" aria-hidden="true"><path d="M1 3h14v10H1zm1.5 1.5v.3L8 8.6l5.5-3.8v-.3zm0 2.1v4.9h11V6.6L8 10.4z"/></svg>
        admin@vomra.com.au
      </li>
    </ul>

    <div class="address-band">42-44 Harbour Lane Eastwood NSW 2122 Australia</div>
  </section>

  <section class="card card--back">
    <div class="brand"><span class="brand__dot"></span>VOMRA</div>
  </section>
</body>
</html>
```